Doctor to Patient Management Website

I need a design for a health management website that connects doctors to patients. The website will consist of: A main page mainly describing our goal, services, and initiatives towards (Who we are AKA "About Us", Our services, Contact Us, Quick Links for health tips, Language selection, Find a doctor, search bar, Member Login Section, small glossary section below with links to all entities mentioned prior, Help section (Helpful tips and tutorials, Used to request help from admin, customer service, to resolve issues or get assistance). A profile page with two types:1) Doctor Profile: Doctor Personal info (First, Last, Middle Name, Title), Clinic, Hospital Info, Department, Credentials, Years of Experience, Patients rating, #Patients seen during the current week, #Patients seen in total, Picture, Link to email doctor, Link to print doctor's profile). Tabs for "About Me", "Contact Info", "Ratings & Comments", "Documents" (To be downloaded and uploaded by patient), "Patients (List of Patients alphabetical order by name)", "Calendar" (to see doctor's availability for booking) underneath all links. 2) Patient profile: About me, Personal Info, Height, Weight, Blood Type, Age, DOB, Name, etc..., Message and email link.Picture of patient with menu made of "Personal Data", "Biometrics", "Allergies", "Illnesses", "Medications", "Medical Procedures", "Doctors" treating the patient, "Documents" (To be downloaded and uploaded by patient). Underneath all, other patients he or she is related to (For example: family member, so patient can't connect to other patients who are family members)3) Login section: New Users will have option to register using:First Name (Required), Last Name, Middle (not required), Address (Not required), City (Required), Country (Required), Email (Not required), Phone Number (Required), Choose UserName, Password, Account Type (Doctor or Patient). Once registered, they will log in using UserName, Password, and Account_Type.Curent Users will log in using UserName, Password, and Account_Type and option to retrieve username or password.Pages to include (Login Page - Registration Page - Retrieve Username and Reset Password Page)Please see link below:https://plumcrate-adwerks.net/importance-claiming-vantorix-quibble-zarn/Pictures are attached to this project as an inspirationFYI: Dummy text can be used to fill in the business, services, and descriptive information. Feel free to include your own ideas in the layout, design, categories, patterns, and more to and showcase your talent. Design and pictures provided are available as source of ideas.

Target Market(s)

Age: 21+ / Family Oriented / Medical Sector / Metropolitan Area / Educated and non Educated Users

Industry/Entity Type

Health Care

Number of Pages Required

5+ page

Font styles to use
Sans Serif

Colors

Designer to choose colors to be used in the design.

Requirements
Must have
• Thin layer design
• Simple font - No serif
• Clean menu with light but solid colors (No Gradient effect)
Nice to have
• Different color themes (2 or 3) can be combined
• Sample pictures for illustration (either as an ad or to go with the flow of your design)
• Dashboard Feel (Suggested but not required)
Should not have
• Artistic fonts - with Serif
• Dark color themes

```html
<!DOCTYPE html>
<html lang="en">
<head>
<meta charset="utf-8">
<title>Velmora — Doctor to Patient Care</title>
<link href="https://fonts.googleapis.com/css2?family=Lato:wght@400;700;900&display=swap" rel="stylesheet">
<style>
:root{
  --blue:#4dbfe9;
  --sky:#67cdf4;
  --gold:#e3bb62;
  --orange:#f7861d;
  --ink:#333333;
  --text:#4a4a4a;
  --grey-band:#f3f3f3;
  --white:#ffffff;
}
*{margin:0;padding:0;box-sizing:border-box}
html,body{width:1200px;height:3046px;overflow:hidden;background:var(--white)}
body{font-family:'Lato',sans-serif;color:var(--text);position:relative}
.abs{position:absolute}
.btn{position:absolute;background:var(--gold);color:var(--white);font-weight:700;font-size:17px;display:flex;align-items:center;justify-content:center;border-radius:2px}
/* header */
.brand{left:75px;top:18px;font-size:44px;font-weight:700;color:#555;letter-spacing:.5px}
.search{left:524px;top:24px;width:331px;height:41px;border:1px solid #ccc;border-radius:3px;font-size:14px;color:#555;padding:12px 14px}
.search svg{position:absolute;right:10px;top:10px}
.member{left:887px;top:26px;width:138px;height:38px;font-size:13px;font-weight:400}
.lang{left:1055px;top:36px;font-size:12px;color:#555;display:flex;align-items:center;gap:8px}
.lang .flag{width:22px;height:14px;background:#3b4f8f}
.nav{left:0;top:90px;width:1200px;height:56px;background:var(--blue)}
.nav ul{list-style:none;display:flex;position:absolute;left:75px;top:20px;gap:0}
.nav li{color:var(--white);font-size:14px;font-weight:700;margin-right:44px}
.find{position:absolute;left:946px;top:0;width:177px;height:56px;background:var(--orange);color:var(--white);font-weight:700;font-size:18px;display:flex;align-items:center;justify-content:center}
/* hero */
.hero{left:0;top:146px;width:1200px;height:564px}
.hero-title{left:0;top:336px;width:1200px;text-align:center;font-size:64px;font-weight:900;color:var(--white)}
.hero-sub{left:0;top:412px;width:1200px;text-align:center;font-size:30px;font-weight:700;color:var(--white)}
/* sections */
h2.sec{position:absolute;font-size:32px;font-weight:400;color:var(--ink)}
p.body{position:absolute;font-size:15px;line-height:28.5px;color:#444}
.lbl{position:absolute;font-size:19px;color:#2aa6db;font-weight:400}
.small{position:absolute;font-size:15px;line-height:24.5px;color:#444}
.card{position:absolute;top:2240px;width:331px;height:420px;background:var(--white)}
.card .photo{width:100%;height:206px}
.card h3{text-align:center;font-size:34px;font-weight:400;color:var(--ink);margin-top:22px}
.card p{text-align:center;font-size:15px;line-height:26.5px;color:#444;margin:14px 24px 0}
/* footer */
.f-head{position:absolute;top:2810px;font-size:13px;font-weight:700;color:#2aa6db}
.f-list{position:absolute;top:2836px;list-style:none;font-size:14px;line-height:27.5px;color:#444}
.social{left:75px;top:2938px;display:flex;gap:18px}
.social span{width:22px;height:22px;border-radius:50%;background:#444;display:block}
</style>
</head>
<body>

<!-- header -->
<div class="abs brand">Velmora</div>
<div class="abs search">Search....
  <svg width="20" height="20" viewBox="0 0 20 20"><circle cx="8" cy="8" r="6" fill="none" stroke="#333" stroke-width="2.4"/><line x1="12.5" y1="12.5" x2="18" y2="18" stroke="#333" stroke-width="2.6"/></svg>
</div>
<div class="btn member">MEMBER LOGIN</div>
<div class="abs lang"><span class="flag"></span>EN
  <svg width="10" height="6"><path d="M1 1l4 4 4-4" stroke="#777" fill="none" stroke-width="1.4"/></svg></div>

<nav class="abs nav">
  <ul><li>HOME</li><li>ABOUT US</li><li>SERVICES</li><li>HEALTH TIPS</li><li>TUTORIALS</li><li>HELP</li><li>GLOSSARY</li><li>CONTACT US</li></ul>
  <div class="find">FIND A DOCTOR</div>
</nav>

<!-- hero -->
<svg class="abs hero" width="1200" height="564" viewBox="0 0 1200 564" role="img" aria-label="Photo of a doctor consulting with an older patient at a desk">
  <defs><linearGradient id="heroG" x1="0" y1="0" x2="1" y2="0">
    <stop offset="0" stop-color="#7f7d7a"/><stop offset=".5" stop-color="#6b5b5b"/><stop offset="1" stop-color="#4d4a3e"/></linearGradient></defs>
  <path d="M0 0H1200V420C1080 390 960 460 820 430C680 400 560 380 420 420C300 455 150 450 0 410Z" fill="url(#heroG)"/>
</svg>
<div class="abs hero-title">WELCOME TO VELMORA</div>
<div class="abs hero-sub">Morbi fringilla velit ac est porttitor consectetur ac eget metus...</div>
<div class="btn" style="left:524px;top:479px;width:152px;height:45px">Read More</div>

<!-- about -->
<h2 class="sec" style="left:75px;top:786px">About Velmora</h2>
<p class="body" style="left:75px;top:838px;width:600px">Lorem ipsum dolor sit amet, consectetur adipiscing elit. Aenean quam arcu, dictum at finibus ac, lobortis vel nisl. Donec ultrices aliquam diam, ac vestibulum nisi rutrum eget. Maecenas nec varius risus. Aliquam eget magna libero. Integer ultricies maximus molestie. Quisque lorem nunc, tincidunt vitae quam eget, egestas interdum tortor. Morbi fringilla velit ac est porttitor consectetur ac eget metus.</p>
<div class="btn" style="left:75px;top:1015px;width:150px;height:47px">Read More</div>
<div class="abs" style="left:704px;top:792px;width:423px;height:270px;background:linear-gradient(180deg,#a7a7ab,#7f7a74)" role="img" aria-label="Photo of wooden blocks stacked with medical symbols"></div>

<!-- what we do -->
<svg class="abs" style="left:0;top:1140px" width="1200" height="620" viewBox="0 0 1200 620">
  <path d="M0 40C200 0 360 60 600 30C820 5 1000 10 1200 45V570C1000 600 820 600 600 575C380 550 200 600 0 570Z" fill="var(--grey-band)"/>
  <path d="M350 570C400 470 500 420 600 420C700 420 800 470 850 570" fill="none" stroke="var(--gold)" stroke-width="2"/>
</svg>
<h2 class="sec" style="left:0;width:1200px;text-align:center;top:1236px">What We Do</h2>
<p class="small" style="left:80px;width:1040px;text-align:center;top:1295px;line-height:29px">Lorem ipsum dolor sit amet, consectetur adipiscing elit. Praesent eu faucibus erat. Nulla facilisi. Proin id accumsan felis, suscipit dignissim nisl. Fusce risus lorem, pharetra sit amet consectetur a, maximus at orci</p>
<div class="lbl" style="left:0;width:1200px;text-align:center;top:1385px">Etiam Euismod</div>
<p class="small" style="left:450px;width:300px;text-align:center;top:1415px">Lorem ipsum dolor sit amet, consectetur adipiscing elit, sed do eiusmod tempor incididunt ut labore..</p>
<div class="lbl" style="left:68px;width:300px;text-align:right;top:1535px">Nulla Imperdiet</div>
<p class="small" style="left:78px;width:290px;text-align:right;top:1565px">Lorem ipsum dolor sit amet, consectetur adipiscing elit, sed do eiusmod tempor incididunt ut labore..</p>
<div class="lbl" style="left:832px;top:1535px">Nulla Imperdiet</div>
<p class="small" style="left:832px;width:290px;top:1565px">Lorem ipsum dolor sit amet, consectetur adipiscing elit, sed do eiusmod tempor incididunt ut labore..</p>
<svg class="abs" style="left:380px;top:1508px" width="440" height="160" viewBox="0 0 440 160">
  <circle cx="219" cy="57" r="51" fill="var(--sky)"/>
  <rect x="204" y="38" width="30" height="38" fill="none" stroke="#fff" stroke-width="3"/>
  <path d="M219 46v12M213 52h12" stroke="#fff" stroke-width="3"/>
  <circle cx="57" cy="104" r="49" fill="#fff" stroke="var(--gold)" stroke-width="2"/>
  <circle cx="57" cy="92" r="9" fill="#333"/><path d="M40 122c0-14 8-20 17-20s17 6 17 20z" fill="#333"/>
  <circle cx="385" cy="104" r="49" fill="#fff" stroke="var(--gold)" stroke-width="2"/>
  <circle cx="385" cy="92" r="9" fill="#333"/><circle cx="369" cy="98" r="7" fill="#333"/><circle cx="401" cy="98" r="7" fill="#333"/>
  <path d="M366 124c0-14 8-20 19-20s19 6 19 20z" fill="#333"/><path d="M355 120c0-10 5-14 12-14h4v14z M415 120c0-10-5-14-12-14h-4v14z" fill="#333"/>
</svg>

<!-- health tips -->
<div class="abs" style="left:75px;top:1813px;width:422px;height:272px;background:linear-gradient(135deg,#cfcfcf,#6f6a63)" role="img" aria-label="Video thumbnail of a doctor on a video call at a computer"></div>
<svg class="abs" style="left:252px;top:1917px" width="64" height="64" viewBox="0 0 64 64"><circle cx="32" cy="32" r="30" fill="#fff"/><path d="M25 19l20 13-20 13z" fill="#333"/></svg>
<h2 class="sec" style="left:524px;top:1806px">Health Tips</h2>
<p class="body" style="left:524px;top:1860px;width:600px">Lorem ipsum dolor sit amet, consectetur adipiscing elit. Aenean quam arcu, dictum at finibus ac, lobortis vel nisl. Donec ultrices aliquam diam, ac vestibulum nisi rutrum eget. Maecenas nec varius risus. Aliquam eget magna libero. Integer ultricies maximus molestie. Quisque lorem nunc, tincidunt vitae quam eget, egestas interdum tortor. Morbi fringilla velit ac est porttitor consectetur ac eget metus.</p>
<div class="btn" style="left:524px;top:2038px;width:152px;height:47px">Read More</div>

<!-- quick links band -->
<svg class="abs" style="left:0;top:2140px" width="1200" height="630" viewBox="0 0 1200 630">
  <path d="M0 40C200 -5 380 50 600 25C830 0 1000 20 1200 45V590C1000 630 820 620 600 595C380 570 200 615 0 590Z" fill="var(--sky)"/>
</svg>
<div class="card" style="left:75px"><div class="photo" style="background:linear-gradient(135deg,#cfe3ee,#4f6f8a)" role="img" aria-label="Photo of medical staff greeting a visitor"></div><h3>Help</h3><p>Lorem ipsum dolor sit amet, consectetur adipiscing elit. Aenean quam arcu, dictum at finibus ac, lobortis vel nisl.</p></div>
<div class="card" style="left:436px"><div class="photo" style="background:linear-gradient(135deg,#eef1f4,#9aa7b4)" role="img" aria-label="Photo of a doctor using a tablet"></div><h3>Glossary</h3><p>Lorem ipsum dolor sit amet, consectetur adipiscing elit. Aenean quam arcu, dictum at finibus ac, lobortis vel nisl.</p></div>
<div class="card" style="left:796px"><div class="photo" style="background:linear-gradient(135deg,#b9c7d6,#2f6a9c)" role="img" aria-label="Photo of a doctor with digital health icons"></div><h3>Tutorials</h3><p>Lorem ipsum dolor sit amet, consectetur adipiscing elit. Aenean quam arcu, dictum at finibus ac, lobortis vel nisl.</p></div>
<div class="btn" style="left:165px;top:2635px;width:150px;height:47px">Read More</div>
<div class="btn" style="left:525px;top:2635px;width:150px;height:47px">Read More</div>
<div class="btn" style="left:886px;top:2635px;width:150px;height:47px">Read More</div>

<!-- footer -->
<div class="abs" style="left:75px;top:2815px;font-size:48px;font-weight:700;color:#555">Velmora</div>
<div class="abs" style="left:75px;top:2875px;font-size:12px;line-height:24px;color:#444">Copyright © 2019, Velmora Care.<br>All Right reserved</div>
<div class="abs social"><span></span><span></span><span></span><span></span><span></span></div>

<div class="f-head" style="left:341px">SITEMAP</div>
<ul class="f-list" style="left:341px"><li>Home</li><li>About Us</li><li>Our Services</li><li>Health Tips</li><li>Tutorials</li></ul>
<ul class="f-list" style="left:473px"><li>Help</li><li>Glossary</li><li>Contact Us</li></ul>
<div class="f-head" style="left:678px">RESOURCES</div>
<ul class="f-list" style="left:678px"><li>Maecenas nec varius</li><li>Aliquam eget</li><li>Magna libero ultricies</li><li>Maximus molestie</li><li>Curabitur consequat</li></ul>
<div class="f-head" style="left:910px">CONTACT INFO</div>
<div class="abs" style="left:910px;top:2836px;font-size:14px;line-height:22px;color:#444"><b style="color:#222">Velmora</b><br>2417 Larchfield Avenue, Suite 300<br>Brookvale, OR 97312<br>USA</div>
<svg class="abs" style="left:910px;top:2942px" width="16" height="16" viewBox="0 0 16 16"><path d="M3 1l3 3-2 2c1 2 3 4 5 5l2-2 3 3-2 3C7 15 1 9 0 4z" fill="#333"/></svg>
<div class="abs" style="left:944px;top:2940px;font-size:14px;color:#444">1-800-555-0147</div>
<svg class="abs" style="left:910px;top:2973px" width="16" height="12" viewBox="0 0 16 12"><rect width="16" height="12" fill="#333"/><path d="M0 0l8 6 8-6" stroke="#fff" fill="none" stroke-width="1.4"/></svg>
<div class="abs" style="left:944px;top:2968px;font-size:14px;color:#444">hello@velmora-care.com</div>

</body>
</html>
```